Professional Business card

I need a business card to send with all my shipments. It needs to look very professional as I am branding myself, more than I am branding my company. The website is not active yet but that along with the instagram is very important as this will be moving shortly. The next required to be included is listed

Target Market(s)

All

Contact Information for Business Card

Very professional and sleek, I am trying to look like the CEO, motivational speaker and future president I plan to be

Colors
ffcf3e

Requirements
Must have
• Front

Dale Wrenfield
CEO
Brivolt Franchiser
Business Consultant/Start Up Guidance
Motivational Speaker
President of The United States 2040
www.dalewrenfield-example.com
[Instagram] @dalewrenfield

Back
I teach the success method used by my company you just bought from. Learn the unique model and start your own Brivolt franchise today
Nice to have
• Black and Gold lettering
Should not have
• Playful vibes

```html
<!DOCTYPE html>
<html lang="en">
<head>
<meta charset="UTF-8">
<title>Dale Wrenfield – Business Card</title>
<link rel="stylesheet" href="https://fonts.googleapis.com/css2?family=Poppins:wght@400;500;600&display=swap">
<style>
  :root {
    --canvas-bg: #1b1b1d;
    --card-black: #1f2022;
    --gold: #d9b45a;
    --gold-line: #e2c36e;
    --gold-light: #fbf3c9;
    --gold-mid: #f1e39f;
    --gold-deep: #e6d38a;
    --ink: #141414;
  }
  * { box-sizing: border-box; margin: 0; padding: 0; }
  html, body {
    width: 1200px;
    height: 800px;
    overflow: hidden;
    background: var(--canvas-bg);
    font-family: "Poppins", sans-serif;
  }
  .canvas {
    width: 1200px;
    height: 800px;
    display: flex;
    align-items: center;
    justify-content: center;
    gap: 48px;
  }
  .card {
    width: 525px;
    height: 300px;
    background: var(--card-black);
    position: relative;
    box-shadow: 0 18px 40px rgba(0, 0, 0, 0.55);
  }
  /* Back side */
  .card-back__frame {
    position: absolute;
    inset: 22px;
    border: 1.5px solid var(--gold-line);
    display: flex;
    align-items: center;
    justify-content: center;
  }
  .card-back__message {
    color: var(--gold);
    font-weight: 500;
    font-size: 14.5px;
    line-height: 1.3;
    text-align: center;
  }
  /* Front side */
  .card-front__panel {
    position: absolute;
    inset: 20px;
    background: linear-gradient(160deg, var(--gold-deep) 0%, var(--gold-light) 35%, var(--gold-mid) 60%, var(--gold-light) 85%, var(--gold-deep) 100%);
    display: flex;
    flex-direction: column;
    align-items: center;
    justify-content: center;
    color: var(--ink);
    text-align: center;
  }
  .card-front__name {
    font-weight: 600;
    font-size: 25px;
    letter-spacing: 0.5px;
    text-transform: uppercase;
    line-height: 1.1;
  }
  .card-front__roles {
    list-style: none;
    font-size: 13px;
    line-height: 1.3;
    margin-top: 2px;
  }
  .card-front__web {
    font-size: 13px;
    letter-spacing: 3px;
    margin-top: 10px;
  }
  .card-front__social {
    display: flex;
    align-items: center;
    gap: 8px;
    font-size: 13px;
    margin-top: 2px;
  }
  .card-front__social-mark {
    width: 11px;
    height: 11px;
    background: var(--ink);
    border-radius: 2px;
  }
</style>
</head>
<body>
  <main class="canvas">
    <section class="card card-back" aria-label="Business card back">
      <div class="card-back__frame">
        <p class="card-back__message">
          I teach the success method used by my company<br>
          you just bought from.<br>
          Learn the unique model and start your<br>
          own Brivolt franchise today
        </p>
      </div>
    </section>

    <section class="card card-front" aria-label="Business card front">
      <div class="card-front__panel">
        <h1 class="card-front__name">Dale Wrenfield</h1>
        <ul class="card-front__roles">
          <li>CEO</li>
          <li>Brivolt Franchiser</li>
          <li>Business Consultant/Start Up Guidance</li>
          <li>Motivational Speaker</li>
          <li>President of The United States 2040</li>
        </ul>
        <p class="card-front__web">www.dalewrenfield-example.com</p>
        <p class="card-front__social"><span class="card-front__social-mark"></span>@dalewrenfield</p>
      </div>
    </section>
  </main>
</body>
</html>
```